Flyer for the Lumen 2025 Conference

I am looking to produce a flyer for our upcoming conference, Lumen 2025. This is an annual conference that we plan to publicize on social media. The ideal designer will create a flyer that is eye-catching and effectively communicates the key information. Please see attached our logo, speaker photo, and flyer content.

Target Market(s)

All demographics

Industry/Entity Type

Christian

Font styles to use
Sans Serif

Requirements
Should not have
• Cross, church

```html
<!DOCTYPE html>
<html lang="en">
<head>
<meta charset="utf-8">
<title>Lumen 2025 Conference Flyer</title>
<link rel="stylesheet" href="https://fonts.googleapis.com/css2?family=Anton&family=Bebas+Neue&family=Montserrat:wght@500;600;700;800&display=swap">
<style>
  :root {
    --backdrop: #c9c9cb;
    --navy-deep: #05070f;
    --navy: #0d1a3d;
    --blue: #1f55b8;
    --blue-bright: #2f7fe0;
    --orange: #f7a21f;
    --orange-deep: #e0701a;
    --orange-light: #fbb332;
    --teal: #45c4d2;
    --white: #ffffff;
    --ink: #111111;
  }
  * { margin: 0; padding: 0; box-sizing: border-box; }
  html, body { width: 911px; height: 1200px; overflow: hidden; background: var(--backdrop); }
  .canvas { position: relative; width: 911px; height: 1200px; }
  .flyer {
    position: absolute; left: 91px; top: 85px; width: 728px; height: 1030px; overflow: hidden;
    background:
      radial-gradient(ellipse 260px 500px at 75% 12%, rgba(47,100,200,0.5), transparent 70%),
      radial-gradient(ellipse 200px 300px at 20% 80%, rgba(40,90,190,0.3), transparent 70%),
      linear-gradient(160deg, var(--navy) 0%, var(--navy-deep) 45%, #0a1433 100%);
  }
  .abs { position: absolute; }
  .speaker-photo {
    left: 370px; top: 160px; width: 358px; height: 870px;
    border-radius: 150px 150px 0 0;
    background:
      radial-gradient(ellipse 90px 100px at 58% 14%, rgba(70,55,45,0.55), transparent 100%),
      linear-gradient(180deg, rgba(31,85,184,0.25) 0%, rgba(31,85,184,0.9) 35%, var(--blue) 60%, rgba(20,60,150,0.85) 85%, rgba(13,26,61,0.5) 100%);
  }
  .brand-name {
    left: 61px; top: 96px; font-family: "Montserrat", sans-serif; font-weight: 600;
    font-size: 46px; color: var(--white); letter-spacing: 1px; line-height: 1;
  }
  .topic { right: 50px; top: 60px; text-align: right; font-family: "Montserrat", sans-serif; font-weight: 700; line-height: 1; }
  .topic-label { color: var(--orange); font-size: 23px; font-weight: 800; }
  .topic-title { color: var(--white); font-size: 24px; margin-top: 1px; line-height: 1; }
  .event-name {
    left: 59px; top: 178px; font-family: "Anton", sans-serif; font-size: 124px; line-height: 1;
    background: linear-gradient(180deg, var(--orange-deep), var(--orange-light) 60%, var(--orange-deep));
    -webkit-background-clip: text; background-clip: text; color: transparent; letter-spacing: 1px;
  }
  .event-year {
    left: 59px; top: 295px; font-family: "Anton", sans-serif; font-size: 176px; line-height: 1;
    color: var(--white); transform: scaleX(0.92); transform-origin: left top;
  }
  .event-kind { left: 56px; top: 468px; font-family: "Bebas Neue", sans-serif; font-size: 84px; line-height: 1; color: var(--teal); }
  .event-type { left: 56px; top: 538px; font-family: "Montserrat", sans-serif; font-weight: 500; font-size: 43px; line-height: 1; color: var(--white); letter-spacing: 1px; }
  .speaker-band {
    left: 52px; top: 613px; width: 326px; height: 74px;
    background: linear-gradient(90deg, var(--orange-deep), var(--orange) 40%, var(--orange-light));
    clip-path: polygon(0 0, 100% 0, 96% 100%, 0 100%);
    padding: 10px 0 0 12px; color: var(--ink);
  }
  .speaker-label { font-family: "Montserrat", sans-serif; font-weight: 700; font-size: 17px; line-height: 1; }
  .speaker-name { font-family: "Anton", sans-serif; font-size: 34px; line-height: 1.1; }
  .schedule { left: 52px; top: 704px; display: grid; grid-template-columns: 173px 173px; grid-auto-rows: 43px; column-gap: 5px; row-gap: 5px; }
  .schedule .cell { height: 43px; display: flex; align-items: center; justify-content: center; overflow: hidden; }
  .schedule .cell b { display: inline-block; font-weight: 400; font-family: "Bebas Neue", sans-serif; font-size: 33px; line-height: 1; white-space: nowrap; transform: scaleX(0.8); }
  .schedule .date { background: linear-gradient(90deg, var(--orange-deep), var(--orange-light)); color: var(--ink); }
  .schedule .time { background: var(--teal); color: var(--white); }
  .venue { left: 52px; top: 867px; font-family: "Montserrat", sans-serif; color: var(--white); line-height: 1.2; }
  .venue-name { font-weight: 800; font-size: 18px; }
  .venue-address { font-weight: 500; font-size: 17.5px; }
  .rule { left: 50px; top: 921px; width: 628px; height: 1px; background: var(--orange); }
  .store-badge { left: 52px; width: 87px; height: 27px; background: var(--white); border-radius: 5px; }
  .app-note { left: 147px; top: 931px; font-family: "Montserrat", sans-serif; color: var(--white); font-weight: 500; font-size: 16px; line-height: 1.4; }
  .app-name { color: var(--orange); font-weight: 800; font-size: 24px; line-height: 1; }
  .contacts { left: 500px; top: 931px; list-style: none; font-family: "Montserrat", sans-serif; font-weight: 500; font-size: 17px; color: var(--white); }
  .contacts li { display: flex; align-items: center; gap: 7px; height: 23px; }
  .contacts svg { width: 17px; height: 17px; flex: none; }
</style>
</head>
<body>
<div class="canvas">
  <div class="flyer">
    <div class="abs speaker-photo" role="img" aria-label="Photo of the speaker, seated, in a blue suit and grey turtleneck"></div>

    <div class="abs brand-name">HALVORA</div>

    <div class="abs topic">
      <div class="topic-label">TOPIC:</div>
      <div class="topic-title">THE VOICE<br>OF THE LORD</div>
    </div>

    <div class="abs event-name">LUMEN</div>
    <div class="abs event-year">2025</div>
    <div class="abs event-kind">A PROPHETIC</div>
    <div class="abs event-type">CONFERENCE</div>

    <div class="abs speaker-band">
      <div class="speaker-label">SPEAKER:</div>
      <div class="speaker-name">PROPHET ELIAS MARREN</div>
    </div>

    <div class="abs schedule">
      <div class="cell date"><b>DECEMBER 26TH</b></div><div class="cell time"><b>6:30PM - 9:00PM</b></div>
      <div class="cell date"><b>DECEMBER 27TH</b></div><div class="cell time"><b>5:30PM - 8:00PM</b></div>
      <div class="cell date"><b>DECEMBER 29TH</b></div><div class="cell time"><b>4:30PM - 7:00PM</b></div>
    </div>

    <div class="abs venue">
      <div class="venue-name">The Northfield Performing Arts Center</div>
      <div class="venue-address">218 Alder Grove Street Northfield, Maine 04120</div>
    </div>

    <div class="abs rule"></div>

    <div class="abs store-badge" style="top:935px"></div>
    <div class="abs store-badge" style="top:966px"></div>

    <div class="abs app-note">
      <div>Download the</div>
      <div class="app-name">HALVORA APP</div>
      <div>to stay updated on the event</div>
    </div>

    <ul class="abs contacts">
      <li><svg viewBox="0 0 20 20"><circle cx="10" cy="10" r="10" fill="#f7a21f"/><rect x="7" y="5" width="6" height="10" rx="1.2" fill="none" stroke="#111" stroke-width="1.2"/></svg>207 555 0184</li>
      <li><svg viewBox="0 0 20 20"><circle cx="10" cy="10" r="10" fill="#f7a21f"/><rect x="5.5" y="6.5" width="9" height="7" fill="none" stroke="#111" stroke-width="1.2"/><path d="M5.5 6.5 10 10.5 14.5 6.5" fill="none" stroke="#111" stroke-width="1.2"/></svg>contact@halvora.org</li>
      <li><svg viewBox="0 0 20 20"><circle cx="10" cy="10" r="10" fill="#f7a21f"/><circle cx="10" cy="10" r="5" fill="none" stroke="#111" stroke-width="1.1"/><ellipse cx="10" cy="10" rx="2.2" ry="5" fill="none" stroke="#111" stroke-width="1.1"/><path d="M5 10h10" stroke="#111" stroke-width="1.1"/></svg>www.halvora.org</li>
    </ul>
  </div>
</div>
</body>
</html>
```